we can communicate on this, but i want to follow the approach we took on Pellew|Marsh & Quinlan but i feel the card front needs the black background and the platinum and gold logo. The back? I am open. we can use the same info from PM&Q. Velmont Arc is an enhanced equity investment fund - basically a very exclusive boutique hedge fund that uses only stock options. very advanced things. hope you are interested

Contact Information for Business Card

Dr. Lewis T. Brennick, CFA
Scientifique de fusée financière
701.555.0143
LTBquant47@mailvantor.com

4718 Willow Creek Bend W.
West Fargo, ND 58078

No web site

Colors

Designer to choose colors to be used in the design.

Requirements
Nice to have
• I tend to prefer the most visible applications of the logo to include logo and name, the logo version with a black background and the gold and platinum components separated by the black. I see this working well for a single side (logo and name - this is card front to me).
• I am fairly open to other treatments on the reverse side with the data. To me, it makes sense to have a different color rendition of the logo on the reverse and it may be a muted black tone on tone or an oversized portion that would have spot UV. Or, the reverse may play with colors and layout
Should not have
• Other colors = no no
• Decorative font

```html
<!DOCTYPE html>
<html lang="en">
<head>
<meta charset="utf-8">
<title>Velmont Arc — Business Card</title>
<link rel="stylesheet" href="https://fonts.googleapis.com/css2?family=Montserrat:wght@500;700&family=Roboto:wght@400&family=Titillium+Web:wght@600&display=swap">
<style>
  :root {
    --backdrop: #3a3a3c;
    --card: #1c1c1e;
    --card-edge: #111113;
    --tone: #2c2c2f;
    --tone-text: #38383b;
    --gold: #d9a92b;
    --gold-deep: #a8781a;
    --platinum: #f2f2f2;
    --text-light: #e8e8e8;
  }
  * { box-sizing: border-box; margin: 0; padding: 0; }
  html, body { width: 799px; height: 1200px; overflow: hidden; }
  body { background: var(--backdrop); position: relative; font-family: "Roboto", sans-serif; }

  .card {
    position: absolute;
    left: 80px;
    width: 640px;
    height: 366px;
    background: var(--card);
    border: 1px solid var(--card-edge);
    box-shadow: 0 18px 40px rgba(0,0,0,0.45);
  }
  .card--front { top: 130px; }
  .card--back { top: 700px; }

  /* Front: tone-on-tone brand */
  .front-brand {
    position: absolute;
    left: 0; right: 0; top: 0; bottom: 0;
    display: flex; align-items: center; justify-content: center; gap: 22px;
  }
  .front-brand__disc {
    width: 120px; height: 120px; border-radius: 50%;
    background: var(--tone);
  }
  .front-brand__name {
    font-family: "Montserrat", sans-serif;
    font-weight: 700;
    font-size: 48px;
    letter-spacing: 2px;
    color: var(--tone-text);
  }

  /* Back: details */
  .holder { position: absolute; left: 42px; top: 112px; }
  .holder__name {
    font-family: "Titillium Web", sans-serif;
    font-weight: 600; font-size: 24px; line-height: 1;
    color: var(--gold);
  }
  .holder__title { margin-top: 6px; font-size: 14px; color: var(--text-light); }

  .rule {
    position: absolute; left: 42px; top: 172px; width: 560px; height: 2px;
    background: linear-gradient(90deg, var(--gold-deep), var(--gold) 40%, rgba(168,120,26,0.15));
  }

  .contact { position: absolute; left: 42px; top: 192px; list-style: none; }
  .contact__item {
    display: flex; align-items: center; gap: 12px;
    font-size: 14px; color: var(--text-light); height: 24px;
  }
  .contact__icon { width: 13px; height: 13px; fill: var(--gold); flex: none; }

  .back-brand {
    position: absolute; right: 40px; top: 82px;
    display: flex; align-items: center; gap: 14px;
  }
  .back-brand__disc { width: 62px; height: 62px; border-radius: 50%; background: var(--gold); }
  .back-brand__name {
    font-family: "Montserrat", sans-serif; font-weight: 700;
    font-size: 30px; letter-spacing: 1px; color: var(--platinum);
  }

  .address {
    position: absolute; right: 40px; top: 262px;
    text-align: right; font-size: 15px; line-height: 1.5; color: var(--text-light);
  }
</style>
</head>
<body>
  <section class="card card--front" aria-label="Card front">
    <div class="front-brand">
      <span class="front-brand__disc"></span>
      <span class="front-brand__name">VELMONT ARC</span>
    </div>
  </section>

  <section class="card card--back" aria-label="Card back">
    <div class="holder">
      <p class="holder__name">Owen Rafe Tully</p>
      <p class="holder__title">Managing Director</p>
    </div>
    <div class="rule"></div>
    <ul class="contact">
      <li class="contact__item">
        <svg class="contact__icon" viewBox="0 0 24 24"><path d="M6.6 10.8a15.1 15.1 0 0 0 6.6 6.6l2.2-2.2a1 1 0 0 1 1-.25 11.4 11.4 0 0 0 3.6.57 1 1 0 0 1 1 1V20a1 1 0 0 1-1 1A17 17 0 0 1 3 4a1 1 0 0 1 1-1h3.5a1 1 0 0 1 1 1c0 1.25.2 2.45.57 3.57a1 1 0 0 1-.25 1z"/></svg>
        828-555-0192
      </li>
      <li class="contact__item">
        <svg class="contact__icon" viewBox="0 0 24 24"><path d="M2 5h20v14H2z M2 5l10 8 10-8" fill="none" stroke="#d9a92b" stroke-width="2.4"/></svg>
        owen@tullyfolio.net
      </li>
    </ul>
    <div class="back-brand">
      <span class="back-brand__disc"></span>
      <span class="back-brand__name">VELMONT ARC</span>
    </div>
    <address class="address" style="font-style:normal">
      519 Harlow Pike, Brennan Falls,<br>
      Kestrel County, US 804217
    </address>
  </section>
</body>
</html>
```